Business cards in digital learning for freelancer

Hello, I need a business cards in french. I work in the Digital learning industries as freeelancer; I'm an expert in digital learning. I work in France. My customer are in the health industry, pharmaceutical industry, and training organization. I've got a logo. I offer three services: consulting, Design, and Training. In the consulting, I offers coaching to choose your digital learning tools and the digital learning strategy. For the Design, I product differents level of elearning like rapid-learning, elearning, micro-learning, video-learning. And for the training service, I've create training about pedagogy, digital learning management project, Digital learning design.
I join my Logo create in this platform. My universe is gamified. I like the life, and I'm very social. I want a card like I'm I. I love Art (painting), Europeen comics. I use in my visual support "permanent maker" font and caracters. I would like cards: elegant, modern, Top class. If you need any information, you can ask me.
thanks for ideas

Target Market(s)

in health industries and training organization for Training manager, instructor, human resources director

Contact Information for Business Card

Phone number : 06 71 38 95 14 , mail: bastiengolmier@quelmoto.fr, web: bastiengolmier.fr , Carrivo

Font styles to use
Sans Serif

Requirements
Must have
• Use my logo and write my 3 services (consulting, training, design)

```html
<!DOCTYPE html>
<html lang="fr">
<head>
<meta charset="utf-8">
<title>Bastien Golmier – Cartes de visite</title>
<link rel="stylesheet" href="https://fonts.googleapis.com/css2?family=Jost:wght@400;600;700&family=Marcellus+SC&display=swap">
<style>
  :root {
    --orange: #e0692a;
    --grey: #6b6b6b;
    --grey-dark: #4f4f4f;
    --grey-soft: #9a9a9a;
    --paper: #fbfbfa;
    --backdrop: #e6e6e4;
  }
  * { box-sizing: border-box; margin: 0; padding: 0; }
  html, body { width: 1200px; height: 801px; overflow: hidden; }
  body {
    background: var(--backdrop);
    font-family: "Jost", sans-serif;
    position: relative;
  }
  .card {
    position: absolute;
    top: 246px;
    width: 540px;
    height: 309px;
    overflow: hidden;
    box-shadow: 0 6px 18px rgba(0,0,0,.14);
  }
  .card--contact { left: 40px; background: var(--paper); }
  .card--brand { left: 620px; background: var(--orange); }

  /* contact side */
  .brand-illustration {
    position: absolute; top: 0; right: 0;
    width: 250px; height: 160px;
    background: linear-gradient(135deg, var(--grey-soft) 0%, var(--grey) 45%, var(--orange) 100%);
    opacity: .85;
  }
  .identity { position: absolute; left: 30px; top: 30px; }
  .identity__name { color: var(--orange); font-size: 22px; font-weight: 600; letter-spacing: .3px; }
  .identity__role { color: var(--grey); font-size: 14px; margin-top: 2px; }

  .contact-list { position: absolute; left: 30px; top: 100px; list-style: none; }
  .contact-list li {
    display: flex; align-items: center; gap: 8px;
    color: var(--grey); font-size: 12.5px; line-height: 21px;
  }
  .contact-list svg { width: 14px; height: 14px; flex: none; }

  .wordmark { position: absolute; right: 28px; bottom: 24px; text-align: center; }
  .wordmark__name {
    font-weight: 700; font-size: 46px; line-height: 1;
    letter-spacing: 3px; color: var(--orange);
  }
  .wordmark__sub {
    display: flex; align-items: center; gap: 8px; justify-content: center;
    font-family: "Marcellus SC", serif; color: var(--grey-dark);
    font-size: 14px; margin-top: 6px;
  }
  .wordmark__sub::before, .wordmark__sub::after {
    content: ""; height: 1px; width: 36px; background: var(--grey-dark);
  }
  .wordmark__services {
    font-family: "Marcellus SC", serif; color: var(--grey-dark);
    font-size: 15px; margin-top: 3px; letter-spacing: .5px;
  }

  /* brand side */
  .brand-lockup {
    position: absolute; inset: 0;
    display: flex; flex-direction: column; align-items: center; justify-content: center;
    color: #fff;
  }
  .brand-lockup__mark {
    width: 86px; height: 86px; border-radius: 50%;
    background: rgba(255,255,255,.9);
    margin-bottom: 14px;
  }
  .brand-lockup__name { font-weight: 700; font-size: 54px; letter-spacing: 4px; line-height: 1; }
  .brand-lockup__services { font-family: "Marcellus SC", serif; font-size: 17px; margin-top: 8px; letter-spacing: .5px; }
</style>
</head>
<body>

<section class="card card--contact">
  <div class="brand-illustration" role="img" aria-label="Illustration de marque : cerveau et arbre stylisés en gris et orange"></div>

  <div class="identity">
    <p class="identity__name">Bastien Golmier</p>
    <p class="identity__role">Digital Learning consultant</p>
  </div>

  <ul class="contact-list">
    <li>
      <svg viewBox="0 0 14 14" aria-hidden="true"><circle cx="7" cy="7" r="7" fill="var(--orange)"/><path d="M4.3 3.6l1.4-.3.7 1.7-.9.6c.4.9 1.1 1.6 2 2l.6-.9 1.7.7-.3 1.4C7 9.4 4.6 7 4.3 3.6z" fill="#fff"/></svg>
      06 71 38 95 14
    </li>
    <li>
      <svg viewBox="0 0 14 14" aria-hidden="true"><circle cx="7" cy="7" r="7" fill="var(--orange)"/><rect x="3.6" y="4.6" width="6.8" height="4.8" fill="none" stroke="#fff" stroke-width=".9"/><path d="M3.6 4.6L7 7.3l3.4-2.7" fill="none" stroke="#fff" stroke-width=".9"/></svg>
      bastiengolmier@quelmoto.fr
    </li>
    <li>
      <svg viewBox="0 0 14 14" aria-hidden="true"><circle cx="7" cy="7" r="7" fill="var(--orange)"/><circle cx="7" cy="7" r="3.4" fill="none" stroke="#fff" stroke-width=".9"/><path d="M3.6 7h6.8M7 3.6c-1.6 2-1.6 4.8 0 6.8M7 3.6c1.6 2 1.6 4.8 0 6.8" fill="none" stroke="#fff" stroke-width=".8"/></svg>
      bastiengolmier.fr
    </li>
    <li>
      <svg viewBox="0 0 14 14" aria-hidden="true"><circle cx="7" cy="7" r="7" fill="var(--orange)"/></svg>
      /carrivo/bastien-golmier
    </li>
  </ul>

  <div class="wordmark">
    <p class="wordmark__name">GOLMIER</p>
    <p class="wordmark__sub">Digital Learning</p>
    <p class="wordmark__services">Consulting, Training, Design</p>
  </div>
</section>

<section class="card card--brand">
  <div class="brand-lockup">
    <div class="brand-lockup__mark" aria-hidden="true"></div>
    <p class="brand-lockup__name">GOLMIER</p>
    <p class="brand-lockup__services">Consulting, Training, Design</p>
  </div>
</section>

</body>
</html>
```